New Business Card Design Project

Need a design that will create an impact / strong impression towards our clients for our business. We are in the lighting business and we do lighting retrofits for large commercial to industrial clientele.

Target Market(s)

Lighting Industry

Industry/Entity Type

Business

Font styles to use
Other font styles liked:
• we would like to use the font on our logo, not sure what it is though..

Requirements
Must have
• Our logo.
Nice to have
• We are open to suggestions that have to do with lighting.

```html
<!DOCTYPE html>
<html lang="en">
<head>
<meta charset="utf-8">
<title>Lumora Retrofit Group – Business Card</title>
<link rel="stylesheet" href="https://fonts.googleapis.com/css2?family=Montserrat:wght@400;500;600&display=swap">
<style>
  :root {
    --page: #d9d6d0;
    --card: #eeede9;
    --green-dark: #1f5e2c;
    --green-mid: #2e8b3a;
    --green-light: #6cc04a;
    --text-grey: #6f6f6c;
    --icon-green: #2a6b35;
  }
  * { margin: 0; padding: 0; box-sizing: border-box; }
  html, body {
    width: 1200px; height: 1047px; overflow: hidden;
    background: var(--page);
    font-family: "Montserrat", sans-serif;
  }
  .card {
    position: absolute; left: 117px; top: 262px;
    width: 966px; height: 522px;
    background: var(--card);
    border-radius: 24px;
    overflow: hidden;
    box-shadow: 0 6px 24px rgba(0,0,0,0.12);
  }
  .brand {
    position: absolute; left: 50px; top: 70px;
    display: flex; align-items: center; gap: 16px;
  }
  .brand-mark {
    width: 44px; height: 44px; background: var(--green-mid);
  }
  .brand-name {
    font-size: 38px; font-weight: 600; color: var(--green-mid);
    letter-spacing: 1px; line-height: 1;
  }
  .holder {
    position: absolute; right: 48px; top: 265px; text-align: right;
  }
  .holder-name {
    font-size: 27px; font-weight: 500; color: var(--green-dark);
    letter-spacing: 1px; line-height: 1.2;
  }
  .holder-title {
    font-size: 21px; font-weight: 400; color: var(--text-grey); line-height: 1.3;
  }
  .divider {
    position: absolute; left: 46px; right: 48px; top: 342px;
    height: 2px; background: var(--green-light);
  }
  .contacts {
    position: absolute; left: 50px; top: 362px; list-style: none;
  }
  .contacts li {
    display: flex; align-items: center; gap: 20px;
    height: 30.5px; font-size: 18px; color: var(--text-grey); letter-spacing: 0.5px;
  }
  .contacts svg { width: 16px; height: 16px; fill: var(--icon-green); }
  .address {
    position: absolute; right: 48px; top: 362px; text-align: right;
    font-size: 18px; color: var(--text-grey); letter-spacing: 0.5px; line-height: 30.5px;
  }
  .band-light {
    position: absolute; left: 0; bottom: 0; width: 700px; height: 13px;
    background: linear-gradient(90deg, var(--green-mid), var(--green-light));
  }
  .band-dark {
    position: absolute; right: 0; bottom: 0; width: 264px; height: 55px;
    background: var(--green-dark);
  }
</style>
</head>
<body>
  <div class="card">
    <div class="brand">
      <div class="brand-mark"></div>
      <div class="brand-name">Lumora Retrofit Group</div>
    </div>

    <div class="holder">
      <div class="holder-name">DANIEL REYES</div>
      <div class="holder-title">Founder</div>
    </div>

    <div class="divider"></div>

    <ul class="contacts">
      <li>
        <svg viewBox="0 0 24 24" aria-hidden="true"><path d="M6.6 10.8a15.1 15.1 0 0 0 6.6 6.6l2.2-2.2a1 1 0 0 1 1-.25 11.4 11.4 0 0 0 3.6.57 1 1 0 0 1 1 1V20a1 1 0 0 1-1 1A17 17 0 0 1 3 4a1 1 0 0 1 1-1h3.5a1 1 0 0 1 1 1c0 1.25.2 2.45.57 3.57a1 1 0 0 1-.25 1z"/></svg>
        0400 555 019
      </li>
      <li>
        <svg viewBox="0 0 24 24" aria-hidden="true"><path d="M2 5h20v2l-10 6L2 7z"/><path d="M2 9l10 6 10-6v10H2z"/></svg>
        info@lumoragroup.com
      </li>
      <li>
        <svg viewBox="0 0 24 24" aria-hidden="true"><path d="M12 2a10 10 0 1 0 0 20 10 10 0 0 0 0-20zm6.9 6h-3a15 15 0 0 0-1.3-4A8 8 0 0 1 18.9 8zM12 4c.9 1.2 1.6 2.6 2 4h-4c.4-1.4 1.1-2.8 2-4zM4.3 14a8 8 0 0 1 0-4h3.4a16 16 0 0 0 0 4zm.8 2h3a15 15 0 0 0 1.3 4A8 8 0 0 1 5.1 16zm3-8h-3a8 8 0 0 1 4.3-4 15 15 0 0 0-1.3 4zM12 20c-.9-1.2-1.6-2.6-2-4h4c-.4 1.4-1.1 2.8-2 4zm2.3-6H9.7a14 14 0 0 1 0-4h4.6a14 14 0 0 1 0 4zm.3 6a15 15 0 0 0 1.3-4h3a8 8 0 0 1-4.3 4zm1.7-6a16 16 0 0 0 0-4h3.4a8 8 0 0 1 0 4z"/></svg>
        www.lumoragroup.com
      </li>
    </ul>

    <div class="address">
      4870 Harbor Lane,<br>
      Suite Mesa 85201
    </div>

    <div class="band-light"></div>
    <div class="band-dark"></div>
  </div>
</body>
</html>
```